Can you make a cool and versatile Tarn Meridian Powerpoint template?
See www.tarnmeridian-example.co.uk and http://www.examplenet.invalid/company/tarn-meridian-ltd/ (on the right) to see how the logos are currently used - with interchangeably white and black backgrounds.
Target Market(s)
Marketing managers, product managers in HR technology, HR consultants
Industry/Entity Type
It Company
Font styles to use
Sans Serif
Requirements
Must have
- Master slide design, fonts, color theme, etc. Ideally two variations - one with white background (using colorful logo), one with a darker background (using black/white logo).

```html
<!DOCTYPE html>
<html lang="en">
<head>
<meta charset="utf-8">
<title>Tarn Meridian – Graphic Slide</title>
<link rel="stylesheet" href="https://fonts.googleapis.com/css2?family=Graduate&family=Open+Sans:wght@400;600&display=swap">
<style>
  :root {
    --page: #ffffff;
    --slide-light: #f2f2f2;
    --slide-mid: #dcdcdc;
    --rule: #333333;
    --band: #333333;
    --brand-blue: #29abe2;
    --brand-blue-dark: #1b75bc;
    --white: #ffffff;
    --green-light: #8dc63f;
    --green-leaf: #39b54a;
    --green-mid: #2db56d;
    --green-dark: #0b9444;
    --teal: #13a89e;
    --tan: #c4996c;
    --tan-dark: #a67c52;
    --grey: #6d6e71;
    --grey-dark: #3d3d3d;
    --slate: #58595b;
    --slate-dark: #3f3f41;
    --gap: #ececec;
  }
  * { margin: 0; padding: 0; box-sizing: border-box; }
  html, body { width: 1200px; height: 900px; overflow: hidden; background: var(--page); }
  .canvas { position: relative; width: 1200px; height: 900px; }
  .slide {
    position: absolute; left: 24px; top: 163px; width: 1152px; height: 647px;
    background: radial-gradient(ellipse at 40% 40%, var(--slide-light), var(--slide-mid));
    overflow: hidden;
  }
  .slide-art { position: absolute; left: 0; top: 0; width: 1152px; height: 647px; }
  .slide-number {
    position: absolute; right: 30px; top: 32px;
    font-family: "Graduate", "Arial Black", sans-serif;
    font-size: 24px; color: var(--white);
  }
  .title-band {
    position: absolute; left: 16px; top: 492px; width: 1122px; height: 145px;
    background: var(--band);
  }
  .slide-title {
    position: absolute; left: 24px; top: 16px;
    font-family: "Graduate", "Arial Black", sans-serif;
    font-size: 66px; line-height: 1; color: var(--brand-blue); letter-spacing: 1px;
  }
  .title-rule {
    position: absolute; left: 24px; top: 92px; width: 506px; height: 3px;
    background: var(--white);
  }
  .slide-subtitle {
    position: absolute; left: 80px; top: 103px;
    font-family: "Open Sans", Arial, sans-serif;
    font-size: 18px; color: var(--white);
  }
  .contact {
    position: absolute; right: 174px; top: 58px; text-align: right;
    font-family: "Open Sans", Arial, sans-serif;
    font-size: 11px; line-height: 17px; color: var(--white);
  }
  .brand-tile {
    position: absolute; right: 12px; top: 12px; width: 146px; height: 122px;
    background: var(--brand-blue);
    display: flex; align-items: center; justify-content: center; text-align: center;
    font-family: "Open Sans", Arial, sans-serif; font-weight: 600;
    font-size: 19px; line-height: 1.2; color: var(--white);
  }
</style>
</head>
<body>
<div class="canvas">
  <section class="slide">
    <svg class="slide-art" viewBox="0 0 1152 647" xmlns="http://www.w3.org/2000/svg" aria-hidden="true">
      <!-- progress rule -->
      <line x1="46" y1="59" x2="1014" y2="59" stroke="var(--rule)" stroke-width="4"/>
      <rect x="32" y="45" width="28" height="28" rx="5" transform="rotate(45 46 59)" fill="var(--white)" stroke="var(--rule)" stroke-width="3"/>
      <circle cx="46" cy="59" r="8" fill="var(--brand-blue)"/>
      <!-- corner tab -->
      <polygon points="1036,14 1138,14 1138,115" fill="var(--brand-blue)"/>

      <!-- pyramid -->
      <g class="pyramid">
        <polygon points="83,424 541,424 528,452 96,452" fill="var(--slate-dark)"/>
        <polygon points="130,353 487,353 541,424 83,424" fill="var(--slate)"/>
        <polygon points="166,343 456,343 449,353 174,353" fill="var(--brand-blue-dark)"/>
        <polygon points="244,267 385,267 456,343 166,343" fill="var(--brand-blue)"/>
        <polygon points="248,257 374,257 369,267 253,267" fill="var(--green-leaf)"/>
        <polygon points="312,186 374,257 248,257" fill="var(--green-light)"/>
      </g>

      <!-- pie chart -->
      <g class="pie" transform="translate(-24 -163)" stroke="var(--gap)" stroke-width="4" stroke-linejoin="round">
        <g transform="translate(6 16)" stroke="none">
          <path d="M857 452 L1025 452 A168 168 0 0 1 965 581 Z" fill="var(--brand-blue-dark)"/>
          <path d="M857 452 L965 581 A168 168 0 0 1 778 600 Z" fill="var(--tan-dark)" transform="translate(-6 0)"/>
          <path d="M857 452 L778 600 A168 168 0 0 1 689 452 Z" fill="var(--grey-dark)" transform="translate(-12 0)"/>
        </g>
        <path d="M857 452 L851 284 A168 168 0 0 1 986 344 Z" fill="var(--green-mid)"/>
        <path d="M857 452 L986 344 A168 168 0 0 1 1025 452 Z" fill="var(--teal)"/>
        <path d="M857 452 L1025 452 A168 168 0 0 1 965 581 Z" fill="var(--brand-blue)"/>
        <path d="M857 452 L965 581 A168 168 0 0 1 778 600 Z" fill="var(--tan)"/>
        <path d="M857 452 L778 600 A168 168 0 0 1 689 452 Z" fill="var(--grey)"/>
        <path d="M857 452 L689 452 A168 168 0 0 1 719 356 Z" fill="var(--green-light)"/>
        <path d="M857 452 L719 356 A168 168 0 0 1 851 284 Z" fill="var(--green-dark)"/>
      </g>
    </svg>

    <span class="slide-number">04</span>

    <footer class="title-band">
      <h1 class="slide-title">GRAPHIC SLIDE</h1>
      <div class="title-rule"></div>
      <p class="slide-subtitle">DETAILS OF SLIDE / NAME OF PRESENTOR</p>
      <p class="contact">WWW.COMPANYSITE.COM<br>COMPANY@COMPANY.COM</p>
      <div class="brand-tile">Tarn<br>Meridian</div>
    </footer>
  </section>
</div>
</body>
</html>
```